Bright Path Mentors Needs A New Website Design

We need a 8 page website designed for "Bright Path Mentors .ca" similar in design to: "keystone learning hub .com".

The winner/successful candidate on the home page will be asked to complete the following inner pages to complete the project:

About Us
Philosophy
How We Work
Work With Us
Blog
Find A Tutor
Contact

Target Market(s)

Tutoring business clients/children

Industry/Entity Type

Education

Number of Pages Required

5+ page

Font styles to use
Sans Serif

Requirements
Must have
• The attached logo included of course. Similar design to the design provided above in the brief. Clear high quality high resolution images of children in school settings.

```html
<!DOCTYPE html>
<html lang="en">
<head>
<meta charset="utf-8">
<title>Bright Path Mentors</title>
<link href="https://fonts.googleapis.com/css2?family=Roboto+Slab:wght@400;700&family=Raleway:wght@400;600;700&family=Roboto:wght@400;500;700&family=Lora:ital@1&family=Kaushan+Script&display=swap" rel="stylesheet">
<style>
:root{
  --blue:#2b3a97;
  --blue-dark:#1f2b78;
  --orange:#f6931e;
  --orange-dark:#d97a0b;
  --white:#ffffff;
  --grey-bg:#ececec;
  --text:#5c5c5c;
  --black:#111111;
}
*{box-sizing:border-box;margin:0;padding:0}
html,body{width:1200px;height:3390px;overflow:hidden}
body{position:relative;font-family:"Raleway",sans-serif;color:var(--text);background:var(--white)}
.abs{position:absolute}
/* header */
.topbar{left:0;top:0;width:1200px;height:62px;background:var(--white)}
.topbar .promo{left:420px;top:14px;font:700 19px "Roboto",sans-serif;color:var(--black)}
.social{display:flex;gap:8px}
.social span{width:30px;height:30px;border-radius:50%;border:2px solid var(--black);display:block}
.topbar .social{left:880px;top:9px}
.assess{left:1078px;top:0;width:122px;height:82px;background:var(--orange);color:var(--white);font:400 20px "Roboto Slab",serif;text-align:center;padding-top:10px;line-height:1.3;clip-path:polygon(0 0,100% 0,100% 100%,50% 88%,0 100%)}
.nav{left:0;top:62px;width:1200px;height:62px;background:var(--blue)}
.nav ul{position:absolute;left:332px;top:22px;display:flex;gap:20px;list-style:none}
.nav li{font:500 14px "Roboto",sans-serif;color:var(--white)}
.logo{left:98px;top:6px;width:176px;height:176px;border-radius:50%;background:var(--white);display:flex;align-items:center;justify-content:center;text-align:center;font:700 21px "Roboto Slab",serif;color:var(--blue);z-index:3;box-shadow:0 2px 8px rgba(0,0,0,.2);line-height:1.2}
/* hero */
.hero{left:0;top:124px;width:1200px;height:560px;background:linear-gradient(120deg,#4a5c7a 0%,#8a6d55 45%,#c9a06b 70%,#6d7f9b 100%)}
.hero .shade{inset:0;background:linear-gradient(90deg,rgba(20,25,50,.55),rgba(20,25,50,0) 60%)}
.hero h2{left:97px;top:135px;font:400 27px "Roboto Slab",serif;color:var(--white)}
.hero h1{left:97px;top:172px;font:700 50px "Roboto Slab",serif;color:var(--white)}
.btn-ghost{left:97px;top:256px;width:198px;height:48px;border:2px solid var(--white);border-radius:24px;color:var(--white);font:500 17px "Roboto",sans-serif;display:flex;align-items:center;justify-content:center}
.arrow{width:22px;height:44px}
.feature{top:388px;width:323px;height:132px;display:flex;align-items:center;padding:0 20px;gap:22px;color:var(--white)}
.feature.blue{background:rgba(43,58,151,.9)}
.feature.orange{background:rgba(246,147,30,.92)}
.feature h3{font:700 19px "Roboto Slab",serif;line-height:1.4}
.feature p{font:400 15px "Roboto",sans-serif;margin-top:8px}
/* personalized */
.h-section{font:700 27px "Roboto Slab",serif;color:var(--blue);letter-spacing:.5px}
.h-section em{font-style:normal;color:var(--orange)}
.rule{height:2px;background:var(--blue);width:160px}
.intro{left:98px;top:725px}
.intro p{width:528px;font-size:12.5px;line-height:1.85;margin-top:14px;color:#777}
.btn-blue{background:var(--blue);color:var(--white);font:700 14px "Roboto",sans-serif;border-radius:22px;display:flex;align-items:center;justify-content:center}
.video{left:694px;top:730px;width:402px;height:282px;background:linear-gradient(135deg,#dbe3ea,#c7d0db 60%,#e9c8a2);border:5px solid #f0f0f0;box-shadow:0 2px 6px rgba(0,0,0,.25)}
.video .play{left:175px;top:112px;width:54px;height:54px;border-radius:50%;background:rgba(0,0,0,.35);border:2px solid var(--white)}
.video .bar{left:0;bottom:0;width:392px;height:22px;background:rgba(30,30,40,.8)}
/* academic */
.academic{left:0;top:1062px;width:1200px;height:460px;background:var(--grey-bg)}
.academic .h-section{position:absolute;left:0;width:1200px;top:35px;text-align:center}
.pin{width:136px;text-align:center}
.pin .circle{width:136px;height:136px;border-radius:50%;border:3px solid var(--blue);background:var(--white);display:flex;align-items:center;justify-content:center;position:relative}
.pin .circle::after{content:"";position:absolute;bottom:-12px;left:58px;width:20px;height:20px;background:inherit;border-right:3px solid var(--blue);border-bottom:3px solid var(--blue);transform:rotate(45deg)}
.pin.active .circle{background:var(--orange);border-color:var(--orange)}
.pin.active .circle::after{border-color:var(--orange)}
.pin p{margin-top:40px;font:400 17px "Roboto Slab",serif;color:var(--blue);line-height:1.6;width:200px;margin-left:-32px}
.pin.active p{color:var(--orange)}
/* why */
.why{left:0;top:1521px;width:1200px;height:532px;background:linear-gradient(180deg,#2f3f9e,#26348a)}
.why h2{position:absolute;width:1200px;text-align:center;top:38px;font:700 27px "Roboto Slab",serif;color:var(--white)}
.point{width:330px;color:var(--white)}
.point h3{font:400 23px "Roboto Slab",serif;line-height:1.2}
.point p{font-size:12px;line-height:1.6;margin-top:8px}
.point.left{text-align:right}
.ico{width:62px;height:62px;border-radius:50%;background:var(--orange);display:flex;align-items:center;justify-content:center}
.shield{left:445px;top:150px;width:312px;height:330px}
.shield .txt{position:absolute;left:0;top:62px;width:312px;text-align:center;font:400 26px "Kaushan Script",cursive;color:var(--blue);line-height:1.55}
.shield .more{left:106px;top:212px;width:100px;height:40px;background:var(--orange);color:var(--white);font:700 14px "Roboto",sans-serif;display:flex;align-items:center;justify-content:center}
/* testimonials */
.testi{left:0;top:2052px;width:1200px;height:400px;background:#f3f3f3}
.testi .h-section{position:absolute;width:1200px;text-align:center;top:50px}
.quote{position:absolute;left:0;width:1200px;top:150px;text-align:center;font:italic 20px "Lora",serif;color:var(--orange);line-height:1.9}
.qmark{font:700 70px "Roboto Slab",serif;color:var(--blue)}
.author{position:absolute;width:1200px;text-align:center;top:252px;font:400 17px "Roboto",sans-serif;color:var(--black)}
.author small{font-size:12px}
/* form */
.inquiry{left:0;top:2452px;width:1200px;height:543px;background:linear-gradient(180deg,#f6a03a,#f39222)}
.inquiry h2{position:absolute;width:1200px;text-align:center;top:48px;font:700 27px "Roboto Slab",serif;color:var(--white)}
.field{left:316px;width:565px;height:40px;background:rgba(120,70,15,.55);border:1px solid rgba(255,255,255,.75);color:var(--white);font:400 13px "Roboto",sans-serif;padding:11px 9px}
.inquiry .btn-submit{left:316px;top:452px;width:565px;height:42px;background:var(--blue);color:var(--white);font:700 14px "Roboto",sans-serif;display:flex;align-items:center;justify-content:center}
/* footer */
.footer{left:0;top:2995px;width:1200px;height:332px;background:var(--black);color:var(--white)}
.f-logo{left:100px;top:70px;width:195px;height:180px;display:flex;flex-direction:column;align-items:center;gap:14px;font:700 24px "Roboto Slab",serif;text-align:center;line-height:1.2}
.f-logo .mark{width:86px;height:86px;border:3px solid var(--white);border-radius:50%}
.footer h4{font:700 16px "Roboto",sans-serif;letter-spacing:.5px}
.footer ul{list-style:none;margin-top:20px}
.footer li{font:400 14px "Raleway",sans-serif;margin-bottom:14px}
.c-row{display:flex;gap:16px;margin-top:20px;font:400 13px "Raleway",sans-serif;line-height:1.5}
.c-row b{font-family:"Roboto",sans-serif}
.c-ico{width:38px;height:38px;border:2px solid var(--white);border-radius:50%;flex:none;display:flex;align-items:center;justify-content:center}
.f-in{border:1px solid #ccc;height:40px;font:400 12px "Roboto",sans-serif;padding:12px 10px}
.f-send{background:var(--orange);width:118px;height:36px;font:700 12px "Roboto",sans-serif;display:flex;align-items:center;justify-content:center}
.copy{left:0;top:3327px;width:1200px;height:63px;background:var(--orange);color:var(--white)}
.copy p{position:absolute;left:98px;top:24px;font-size:13px}
.cards{left:705px;top:16px;display:flex;gap:8px}
.cards span{width:52px;height:30px;border-radius:4px;background:var(--white)}
.copy .social{left:945px;top:16px}
.copy .social span{border-color:var(--white)}
</style>
</head>
<body>

<header>
  <div class="abs topbar">
    <p class="abs promo">"First Session Just $35 - Call 1-855-310-4472 Now"</p>
    <div class="abs social"><span></span><span></span><span></span><span></span><span></span></div>
  </div>
  <div class="abs nav">
    <ul><li>HOME</li><li>ABOUT US</li><li>PHILOSOPHY</li><li>HOW WE WORK</li><li>WORK WITH US</li><li>BLOG</li><li>FIND A TUTOR</li><li>CONTACT</li></ul>
  </div>
  <div class="abs logo">BRIGHT PATH<br>MENTORS</div>
  <div class="abs assess">Free<br>Assessment</div>
</header>

<section class="abs hero" role="img" aria-label="Photo of a smiling boy raising his hand in a classroom with classmates behind">
  <div class="abs shade"></div>
  <h2 class="abs">BETTER EDUCATION FOR A</h2>
  <h1 class="abs">BETTER WORLD</h1>
  <div class="abs btn-ghost">LEARN WITH US</div>
  <svg class="abs arrow" style="left:24px;top:256px" viewBox="0 0 22 44"><path d="M20 2 2 22l18 20" fill="none" stroke="#fff" stroke-width="3"/></svg>
  <svg class="abs arrow" style="left:1154px;top:256px" viewBox="0 0 22 44"><path d="M2 2l18 20L2 42" fill="none" stroke="#fff" stroke-width="3"/></svg>
  <div class="abs feature blue" style="left:98px">
    <svg width="60" height="50" viewBox="0 0 60 50"><path d="M30 6 2 18l28 12 28-12z" fill="#fff"/><path d="M14 24v12c8 8 24 8 32 0V24l-16 7z" fill="#fff"/><path d="M54 19v16" stroke="#fff" stroke-width="3"/></svg>
    <div><h3>MAKING PARENTS &amp;<br>KIDS HAPPY</h3><p>Our Reviews</p></div>
  </div>
  <div class="abs feature orange" style="left:438px">
    <svg width="60" height="50" viewBox="0 0 60 50"><rect x="10" y="6" width="40" height="28" fill="none" stroke="#fff" stroke-width="3"/><circle cx="18" cy="40" r="5" fill="#fff"/><circle cx="42" cy="40" r="5" fill="#fff"/><path d="M18 26h24" stroke="#fff" stroke-width="3"/></svg>
    <div><h3>TUTORING WITH A<br>PERSONAL TOUCH</h3><p>How We Work</p></div>
  </div>
  <div class="abs feature blue" style="left:775px">
    <svg width="60" height="50" viewBox="0 0 60 50"><rect x="12" y="4" width="34" height="42" rx="3" fill="none" stroke="#fff" stroke-width="3"/><path d="M19 16h20M19 25h20M19 34h12" stroke="#fff" stroke-width="3"/></svg>
    <div><h3>SATISFACTION<br>GURANTEED</h3><p>Find Your Tutor</p></div>
  </div>
</section>

<section class="abs intro">
  <h2 class="h-section">PERSONALIZED <em>TUTORING</em></h2>
  <div class="rule" style="margin-top:8px"></div>
  <p>Facing academic challenges together to boost confidence and build success in children. Bright Path Mentors seeks to do away with the bad rap and stigma of tutoring, to give clients a fresh perspective on this staple of education. Hearing a lesson in a personalized, easy to understand way, in a location convenient, even comfortable to the student often makes the difference between frustration and academic victory.</p>
  <p style="margin-top:6px">To be honest, we all need help sometimes, and Bright Path Mentors exists to provide it in the world of academia. We believe that within every child lies the potential.</p>
  <div class="btn-blue" style="width:162px;height:42px;margin-top:22px">START CHATTING</div>
</section>
<div class="abs video" role="img" aria-label="Video still of a cartoon teacher with children at a chalkboard">
  <div class="abs play"></div>
  <div class="abs bar"></div>
</div>

<section class="abs academic">
  <h2 class="h-section">ACADEMIC <em>TUTORING</em></h2>
  <div class="abs rule" style="left:520px;top:88px"></div>
  <svg class="abs arrow" style="left:34px;top:194px" viewBox="0 0 22 44"><path d="M20 2 2 22l18 20" fill="none" stroke="#333" stroke-width="2.5"/></svg>
  <svg class="abs arrow" style="left:1144px;top:194px" viewBox="0 0 22 44"><path d="M2 2l18 20L2 42" fill="none" stroke="#333" stroke-width="2.5"/></svg>
  <div class="abs pin" style="left:113px;top:146px"><div class="circle"><svg width="62" height="56" viewBox="0 0 62 56"><path d="M31 2 4 16h54z" fill="#2b3a97"/><path d="M10 20v26M20 20v26M31 20v26M42 20v26M52 20v26" stroke="#2b3a97" stroke-width="5"/><rect x="4" y="48" width="54" height="6" fill="#2b3a97"/></svg></div><p>JK to Grade 12</p></div>
  <div class="abs pin active" style="left:328px;top:146px"><div class="circle"><svg width="62" height="52" viewBox="0 0 62 52"><rect x="6" y="4" width="50" height="12" rx="2" fill="none" stroke="#fff" stroke-width="4"/><rect x="10" y="20" width="46" height="12" rx="2" fill="none" stroke="#fff" stroke-width="4"/><rect x="4" y="36" width="54" height="12" rx="2" fill="none" stroke="#fff" stroke-width="4"/></svg></div><p>All Subjects - Math, English, French, Science and More!</p></div>
  <div class="abs pin" style="left:531px;top:146px"><div class="circle"><svg width="66" height="52" viewBox="0 0 60 50"><path d="M30 6 2 18l28 12 28-12z" fill="#2b3a97"/><path d="M14 24v12c8 8 24 8 32 0V24l-16 7z" fill="#2b3a97"/></svg></div><p>We Work With Your Student's Current Class Curriculum</p></div>
  <div class="abs pin" style="left:734px;top:146px"><div class="circle"><svg width="52" height="60" viewBox="0 0 52 60"><rect x="4" y="8" width="40" height="48" rx="3" fill="none" stroke="#2b3a97" stroke-width="4"/><path d="M12 22h6M22 22h14M12 34h6M22 34h14M12 46h6M22 46h14" stroke="#2b3a97" stroke-width="4"/></svg></div><p>ACT/SAT Test Prep</p></div>
  <div class="abs pin" style="left:942px;top:146px"><div class="circle"><svg width="66" height="48" viewBox="0 0 66 48"><circle cx="33" cy="12" r="8" fill="#2b3a97"/><circle cx="14" cy="16" r="6" fill="#2b3a97"/><circle cx="52" cy="16" r="6" fill="#2b3a97"/><path d="M20 42c0-14 26-14 26 0zM2 40c0-10 20-10 20 0zM44 40c0-10 20-10 20 0z" fill="#2b3a97"/></svg></div><p>In-Home Tutoring We Come to You</p></div>
</section>

<section class="abs why">
  <h2>WHY BRIGHT PATH MENTORS?</h2>
  <div class="abs rule" style="left:520px;top:90px;background:var(--white)"></div>
  <div class="abs point left" style="left:16px;top:190px"><h3>Ontario Certified<br>Teachers</h3><p>The up-to-date training, qualifications and experience of our tutors ensures student success.</p></div>
  <div class="abs ico" style="left:360px;top:190px"><svg width="30" height="30" viewBox="0 0 30 30"><rect x="3" y="4" width="24" height="16" fill="none" stroke="#fff" stroke-width="2.5"/><path d="M8 26h14M15 20v6" stroke="#fff" stroke-width="2.5"/></svg></div>
  <div class="abs point left" style="left:16px;top:335px"><h3>Time and Space<br>Flexibility</h3><p>Our tutors travel to meet at a time and place convenient to you. Yes, we fit into your schedule.</p></div>
  <div class="abs ico" style="left:360px;top:335px"><svg width="30" height="30" viewBox="0 0 30 30"><circle cx="15" cy="9" r="6" fill="#fff"/><path d="M4 28c0-12 22-12 22 0z" fill="#fff"/></svg></div>
  <div class="abs shield">
    <svg width="312" height="330" viewBox="0 0 312 330"><path d="M20 10h272l12 20c-10 150-60 240-148 292C68 270 18 180 8 30z" fill="#fff" stroke="#2b3a97" stroke-width="3"/><path d="M32 22h248l8 14c-10 136-56 220-132 272C80 256 34 172 24 36z" fill="none" stroke="#2b3a97" stroke-width="2"/></svg>
    <div class="txt">What Bright Path<br>Mentors Offers Your<br>Child?</div>
    <div class="abs more">Read More</div>
  </div>
  <div class="abs ico" style="left:779px;top:190px"><svg width="30" height="30" viewBox="0 0 30 30"><circle cx="15" cy="9" r="6" fill="#fff"/><path d="M4 28c0-12 22-12 22 0z" fill="#fff"/></svg></div>
  <div class="abs point" style="left:861px;top:190px"><h3>One-on-One<br>Attention</h3><p>With professionalism and personalized attention our tutors seek to develop a relationship with your child.</p></div>
  <div class="abs ico" style="left:779px;top:335px"><svg width="30" height="30" viewBox="0 0 30 30"><path d="M6 14h5v13H6zM13 14l5-10c3 0 4 2 3 6h6l-2 17H13z" fill="#fff"/></svg></div>
  <div class="abs point" style="left:861px;top:335px"><h3>A Confidence Boost</h3><p>Children who successfully tackle challenges in their lives boost their confidence and willingness to take</p></div>
</section>

<section class="abs testi">
  <h2 class="h-section">READ OUR <em>TESTIMONIALS</em></h2>
  <div class="abs rule" style="left:520px;top:100px"></div>
  <span class="abs qmark" style="left:162px;top:118px">&ldquo;</span>
  <p class="quote">Maria Delgado Dear Ms. Delgado: RE: Highest Recommendation for Tutoring Services<br>I take this opportunity to give the highest...</p>
  <span class="abs qmark" style="left:944px;top:160px">&rdquo;</span>
  <p class="author">Laura M. <small>(LAKEVIEW, ONTARIO)</small></p>
  <div class="abs btn-blue" style="left:488px;top:296px;width:224px;height:48px;font-size:15px;font-weight:500;border-radius:24px">Read More Testimonials</div>
</section>

<section class="abs inquiry" role="img" aria-label="Orange backdrop of a child writing sums at a desk">
  <h2>GENERAL INQUIRY FORM</h2>
  <div class="abs rule" style="left:520px;top:92px;background:var(--white)"></div>
  <div class="abs field" style="top:136px">Name</div>
  <div class="abs field" style="top:188px">Email</div>
  <div class="abs field" style="top:240px">Telephone</div>
  <div class="abs field" style="top:292px">Postal Code</div>
  <div class="abs field" style="top:344px">Iam a:<svg class="abs" style="right:10px;top:16px" width="10" height="6" viewBox="0 0 10 6"><path d="M0 0h10L5 6z" fill="#fff"/></svg></div>
  <div class="abs field" style="top:396px">Message</div>
  <div class="abs btn-submit">CONTACT BRIGHT PATH MENTORS</div>
</section>

<footer class="abs footer">
  <div class="abs f-logo"><div class="mark"></div>BRIGHT PATH<br>MENTORS</div>
  <div class="abs" style="left:373px;top:48px">
    <h4>QUICK LINKS</h4>
    <ul><li>› Home</li><li>› About Us</li><li>› Philosophy</li><li>› How We Work</li><li>› Work With Us</li><li>› Contact Us</li></ul>
  </div>
  <div class="abs" style="left:565px;top:48px;width:220px">
    <h4>CONTACT US</h4>
    <div class="c-row"><div class="c-ico"><svg width="14" height="18" viewBox="0 0 14 18"><path d="M7 1a6 6 0 0 0-6 6c0 5 6 10 6 10s6-5 6-10a6 6 0 0 0-6-6z" fill="#fff"/></svg></div><p><b>BRIGHTPATHMENTORS,</b><br>1275 Maple Ridge Ave #210,<br>Northfield, ON M2B</p></div>
    <div class="c-row"><div class="c-ico"><svg width="12" height="18" viewBox="0 0 12 18"><rect x="1" y="1" width="10" height="16" rx="2" fill="none" stroke="#fff" stroke-width="2"/></svg></div><p><b>PHONE:</b><br>1-855-310-4472</p></div>
    <div class="c-row"><div class="c-ico"><svg width="18" height="13" viewBox="0 0 18 13"><rect x="1" y="1" width="16" height="11" fill="#fff"/><path d="M1 1l8 6 8-6" stroke="#111" stroke-width="1.5" fill="none"/></svg></div><p><b>Mail:</b><br>info@brightpathmentors.ca</p></div>
  </div>
  <div class="abs" style="left:814px;top:48px;width:286px">
    <h4>WORK WITH US</h4>
    <div style="display:flex;gap:8px;margin-top:20px"><div class="f-in" style="width:139px">Name</div><div class="f-in" style="width:139px">Phone</div></div>
    <div class="f-in" style="margin-top:8px;position:relative">Upload Resume<svg style="position:absolute;right:10px;top:12px" width="14" height="14" viewBox="0 0 14 14"><circle cx="7" cy="4" r="3.5" fill="#fff"/><path d="M0 14c0-7 14-7 14 0z" fill="#fff"/></svg></div>
    <div class="f-in" style="margin-top:8px;height:66px">Message</div>
    <div class="f-send" style="margin-top:12px">SUBMIT NOW</div>
  </div>
</footer>

<div class="abs copy">
  <p>Copyright © 2016 Bright Path Mentors. All Right Reserved</p>
  <div class="abs cards"><span style="width:90px;background:transparent;border:2px solid #fff"></span><span></span><span></span><span></span></div>
  <div class="abs social"><span></span><span></span><span></span><span></span><span></span></div>
</div>

</body>
</html>
```